Velmoria-Quillmesh Partial Redesign - Web App

Are you able to apply your creativity to an existing layout? I’m convinced that even just a few touches can make a big difference to add personality and professionalism to a website design, and I’m looking for someone able to use existing ideas and bring them to the next level while keeping inside some given constraints.
The actual job is to improve an existing design concept and to apply it creatively to a landing page, a simple home page, and an older web app (single page website).
To help you start with a clear picture of the current situation and of my requirements, I created a detailed brief with screenshots, live examples, and complete instructions. You can find it attached to this job.
My tastes are inclined towards clean and simple designs. For this project I'm not looking for dazzling novelty, but for very solid craftsmanship. Are the right man - or woman - for the job?
Updates
I wanted to thank everybody who participated in this project. I made a choice, but also other designs were interesting. Hope to work with you another time.
Target Market(s)
Our main target is social media marketers and startuppers
Look and feel
Each slider illustrates characteristics of the customer's brand and the style your logo design should communicate.

```html
<!DOCTYPE html>
<html lang="en">
<head>
<meta charset="utf-8">
<title>Quillmesh.me – #Hollywood</title>
<link href="https://fonts.googleapis.com/css2?family=Arimo:ital,wght@0,400;0,700;1,400&family=Noto+Serif:ital@1&display=swap" rel="stylesheet">
<style>
:root{
  --bar:#1c1c1c;
  --bar-top:#3a3a3a;
  --ink:#333;
  --head-blue:#2d5f86;
  --accent:#1d8ad6;
  --accent-dark:#1673b8;
  --pro:#59a879;
  --sky-top:#2b9be4;
  --sky-mid:#8ccaf3;
  --ball:#c5f7df;
  --ball-edge:#b4eed2;
  --tag:#2e8a5c;
  --core:#a259f0;
  --link:#8a7b86;
  --card-top:#f2f2f2;
  --card-bot:#c9c9c9;
  --tweet-ink:#333;
  --tweet-link:#1a8fd9;
  --footer:#232323;
  --footer-deep:#151515;
  --footer-ink:#e8e8e8;
  --muted:#8a8a8a;
  --cyan:#2fa3d6;
}
*{box-sizing:border-box;margin:0;padding:0}
html,body{width:1200px;height:1064px;overflow:hidden}
body{position:relative;font-family:"Arimo",Arial,sans-serif;color:var(--ink);background:#fff}
.abs{position:absolute}

/* header */
.topbar{left:0;top:0;width:1200px;height:43px;background:linear-gradient(var(--bar-top),var(--bar))}
.brand{left:216px;top:9px;display:flex;align-items:center;gap:10px;color:#fff}
.brand-dot{width:22px;height:22px;border-radius:50%;border:2px solid #ddd}
.brand-name{font-weight:700;font-size:18px;color:#fff}
.tagline{left:414px;top:13px;color:#fff;font-style:italic;font-size:15px}
.nav a{position:absolute;top:15px;color:#ddd;font-weight:700;font-size:12px;text-decoration:none}
.user-btn{left:926px;top:6px;width:48px;height:30px;border-radius:4px;background:#111;border:1px solid #444}

/* data bar */
.databar{left:0;top:43px;width:1200px;height:74px;background:linear-gradient(#fff,#f0f0f0)}
.data-title{left:223px;top:56px;font-size:14px;color:var(--head-blue);font-weight:700}
.data-title b{color:var(--accent-dark)}
.tab{position:absolute;top:78px;height:21px;border:1px solid #ccc;border-radius:2px;background:#fff;display:flex;font-size:9px;color:#666}
.tab span{padding:0 9px;line-height:19px}
.tab .free{margin-left:auto;background:var(--accent);color:#fff}
.tab .pro{margin-left:auto;background:var(--pro);color:#fff}
.popularity{left:751px;top:56px;font-size:14px;font-weight:700;color:var(--head-blue)}
.search-input{left:751px;top:77px;width:155px;height:23px;border:1px solid #ccc;border-radius:12px;background:#f7f7f7}
.search-btn{left:915px;top:78px;width:60px;height:21px;border-radius:11px;background:var(--accent);color:#fff;font-size:10px;font-weight:700;text-align:center;line-height:21px}

/* sky band */
.sky{left:0;top:117px;width:1200px;height:190px;background:linear-gradient(var(--sky-top),var(--sky-mid) 55%,#fff)}
.section-title{font-size:15px;font-weight:700;color:#2a2a2a}
.graph-title{left:216px;top:138px}
.tweets-title{left:759px;top:138px}
.hint{left:216px;top:170px;width:336px;height:32px;border:1px solid #a9d8f3;border-radius:3px;background:linear-gradient(#e6f5fe,#c6e8fb);font-size:10px;color:#2b4f6a;line-height:30px;padding-left:30px;z-index:2}
.hint i{position:absolute;left:12px;color:var(--accent);font-weight:700}
.hint .close{position:absolute;right:10px;top:9px;width:11px;height:11px;border-radius:50%;background:#8fb6cf}

.graph{left:200px;top:160px}
.mode{top:681px;height:27px;font-size:11px;text-align:center;line-height:27px}
.mode.on{left:379px;width:101px;background:var(--accent);color:#fff;border-radius:3px 0 0 3px}
.mode.off{left:480px;width:101px;background:#f3f3f3;color:#888;border:1px solid #ccc;border-radius:0 3px 3px 0}

/* tweets */
.tweet{position:absolute;left:761px;width:222px;height:76px;border:1px solid #bbb;background:linear-gradient(var(--card-top),var(--card-bot));box-shadow:0 1px 3px rgba(0,0,0,.25)}
.avatar{position:absolute;left:-5px;top:13px;width:50px;height:47px;background:linear-gradient(#8b9aa6,#5d5a57);border:2px solid #eee;box-shadow:0 1px 2px rgba(0,0,0,.4)}
.tweet p{position:absolute;left:50px;top:12px;width:170px;font-family:"Noto Serif",Georgia,serif;font-style:italic;font-size:9.6px;line-height:16px;color:var(--tweet-ink)}
.tweet p a{color:var(--tweet-link);text-decoration:none}
.tweet .time{position:absolute;left:50px;top:46px;font-size:9px;color:#999}
.tweet .time::before{content:"";display:inline-block;width:9px;height:7px;border-radius:50%;background:#aaa;margin-right:4px}

/* footer */
.footer{left:0;top:740px;width:1200px;height:284px;background:linear-gradient(#2c2c2c,var(--footer));border-top:3px solid #444}
.footer h3{position:absolute;top:761px;font-size:18px;font-weight:400;color:#fff}
.rule{position:absolute;top:790px;height:1px;background:#3d3d3d}
.reach li{position:absolute;left:256px;list-style:none;font-size:11.5px;color:var(--footer-ink)}
.reach svg{position:absolute;left:-27px;top:0}
.about-mark{left:486px;top:810px;width:80px;height:50px;display:flex;align-items:center;justify-content:center}
.about-mark span{width:34px;height:34px;border-radius:50%;border:2px solid #ccc}
.about-text{left:482px;top:805px;width:230px;font-size:11.5px;line-height:17.6px;color:var(--footer-ink);letter-spacing:.2px}
.about-text .float{float:left;width:98px;height:56px}
.field{position:absolute;left:744px;width:232px;background:#1b1b1b;border:1px solid #333;border-radius:3px;font-size:9.5px;color:#ddd;padding:8px 14px;box-shadow:inset 0 1px 3px #000}
.required{left:748px;top:981px;font-size:9.5px;color:var(--cyan)}
.send{left:925px;top:978px;width:50px;height:18px;background:var(--cyan);color:#fff;font-size:10px;text-align:center;line-height:18px;border-radius:2px}
.bottombar{left:0;top:1024px;width:1200px;height:40px;background:var(--footer-deep)}
.copyright{left:226px;top:1041px;font-size:8px;color:var(--muted)}
.bottom-links{right:222px;top:1041px;font-size:8px;color:var(--muted)}
.bottom-links span{margin:0 6px}
</style>
</head>
<body>

<header class="abs topbar"></header>
<div class="abs brand"><span class="brand-dot"></span><span class="brand-name">Quillmesh.me</span></div>
<div class="abs tagline">explore the hashtagspace</div>
<nav class="nav">
  <a style="left:737px">Blog</a><a style="left:796px">About</a><a style="left:864px">Help</a>
</nav>
<div class="abs user-btn">
  <svg width="48" height="30" viewBox="0 0 48 30"><circle cx="18" cy="11" r="4" fill="#fff"/><path d="M11 22c0-5 14-5 14 0z" fill="#fff"/><path d="M31 13h7l-3.5 4z" fill="#fff"/></svg>
</div>

<section class="abs databar"></section>
<div class="abs data-title">Data for <b>#Hollywood</b></div>
<div class="tab" style="left:224px;width:139px"><span>Top Related Hashtag</span><span class="free">FREE</span></div>
<div class="tab" style="left:370px;width:116px"><span>Top Influencers</span><span class="free">FREE</span></div>
<div class="tab" style="left:494px;width:83px"><span>Varians</span><span class="free">FREE</span></div>
<div class="tab" style="left:585px;width:140px"><span>In-Depth Intellegence</span><span class="pro">PRO</span></div>
<div class="abs popularity">Popularity 65.9</div>
<div class="abs search-input"></div>
<div class="abs search-btn">SEARCH</div>

<div class="abs sky" role="img" aria-label="Soft blue sky with white clouds"></div>
<h2 class="abs section-title graph-title">The TOP 10 related hashtags for #hollywood</h2>
<h2 class="abs section-title tweets-title">TOP RECENT TWEETS</h2>

<svg class="abs graph" width="560" height="520" viewBox="200 160 560 520" font-family="Arimo, Arial, sans-serif" font-size="7" font-weight="700">
  <g stroke="var(--link)" stroke-opacity=".45" stroke-width="2.2">
    <line x1="476" y1="426" x2="389" y2="242"/><line x1="476" y1="426" x2="553" y2="214"/>
    <line x1="476" y1="426" x2="290" y2="338"/><line x1="476" y1="426" x2="541" y2="344" stroke-width="4"/>
    <line x1="476" y1="426" x2="695" y2="330"/><line x1="476" y1="426" x2="254" y2="462" stroke-width="3"/>
    <line x1="476" y1="426" x2="693" y2="470" stroke-width="4"/><line x1="476" y1="426" x2="347" y2="558"/>
    <line x1="476" y1="426" x2="603" y2="570" stroke-width="4"/><line x1="476" y1="426" x2="470" y2="623" stroke-width="3"/>
  </g>
  <g fill="var(--ball)" fill-opacity=".95">
    <circle cx="389" cy="242" r="55"/><circle cx="553" cy="214" r="44"/><circle cx="290" cy="338" r="35"/>
    <circle cx="541" cy="344" r="42"/><circle cx="695" cy="330" r="46"/><circle cx="254" cy="462" r="46"/>
    <circle cx="693" cy="470" r="42"/><circle cx="347" cy="558" r="38"/><circle cx="603" cy="570" r="37"/>
    <circle cx="470" cy="623" r="49"/>
  </g>
  <circle cx="476" cy="426" r="38" fill="var(--core)"/>
  <g fill="var(--tag)">
    <rect x="355" y="237" width="67" height="13" rx="2"/><rect x="534" y="211" width="38" height="12" rx="2"/>
    <rect x="276" y="334" width="29" height="12" rx="2"/><rect x="527" y="339" width="28" height="12" rx="2"/>
    <rect x="663" y="326" width="65" height="12" rx="2"/><rect x="238" y="458" width="33" height="12" rx="2"/>
    <rect x="681" y="468" width="24" height="12" rx="2"/><rect x="334" y="554" width="26" height="12" rx="2"/>
    <rect x="587" y="568" width="32" height="12" rx="2"/><rect x="455" y="619" width="31" height="12" rx="2"/>
    <rect x="455" y="421" width="42" height="13" rx="2"/>
  </g>
  <g fill="#fff" text-anchor="middle">
    <text x="388" y="247">teamfollowback</text><text x="553" y="220">fashion</text>
    <text x="290" y="343">retail</text><text x="541" y="348">sexy</text>
    <text x="695" y="335">autofollowback</text><text x="254" y="467">music</text>
    <text x="693" y="477">hot</text><text x="347" y="563">sales</text>
    <text x="603" y="577">gossip</text><text x="470" y="628">news</text>
    <text x="476" y="431">celebrity</text>
  </g>
</svg>
<div class="abs hint"><i>i</i>To explore the hashtag, click on the balls<span class="close"></span></div>
<div class="abs mode on">Simple Mode</div>
<div class="abs mode off">Advanced Mode</div>

<div class="tweet" style="top:171px"><div class="avatar" role="img" aria-label="User profile photo"></div><p>Marla Vance and Juno Reyes have a mustard-off <a>@tidelark</a> #hollywood</p><div class="time">2 hours ago</div></div>
<div class="tweet" style="top:259px"><div class="avatar" role="img" aria-label="User profile photo"></div><p>Marla Vance and Juno Reyes have a mustard-off <a>@tidelark</a> #hollywood</p><div class="time">2 hours ago</div></div>
<div class="tweet" style="top:348px"><div class="avatar" role="img" aria-label="User profile photo"></div><p>Marla Vance and Juno Reyes have a mustard-off <a>@tidelark</a> #hollywood</p><div class="time">2 hours ago</div></div>
<div class="tweet" style="top:437px"><div class="avatar" role="img" aria-label="User profile photo"></div><p>Marla Vance and Juno Reyes have a mustard-off <a>@tidelark</a> #hollywood</p><div class="time">2 hours ago</div></div>
<div class="tweet" style="top:525px"><div class="avatar" role="img" aria-label="User profile photo"></div><p>Marla Vance and Juno Reyes have a mustard-off <a>@tidelark</a> #hollywood</p><div class="time">2 hours ago</div></div>
<div class="tweet" style="top:614px"><div class="avatar" role="img" aria-label="User profile photo"></div><p>Marla Vance and Juno Reyes have a mustard-off <a>@tidelark</a> #hollywood</p><div class="time">2 hours ago</div></div>

<footer class="abs footer"></footer>
<h3 style="left:228px">Reach Us</h3>
<h3 style="left:486px">About Us</h3>
<h3 style="left:744px;top:763px">Contact Us</h3>
<div class="rule" style="left:228px;width:228px"></div>
<div class="rule" style="left:486px;width:230px"></div>
<div class="rule" style="left:744px;width:232px"></div>

<ul class="reach">
  <li style="top:812px"><svg width="17" height="12" viewBox="0 0 17 12"><rect x="1" y="1" width="15" height="10" fill="none" stroke="#ccc" stroke-width="1.5"/><path d="M1 1l7.5 6L16 1" fill="none" stroke="#ccc" stroke-width="1.5"/></svg>info@velmoria.com</li>
  <li style="top:836px"><svg width="14" height="14" viewBox="0 0 14 14"><path d="M3 1l3 3-2 2c1 2 2 3 4 4l2-2 3 3-2 2C6 13 1 8 1 3z" fill="#ccc"/></svg>555-010-4821</li>
  <li style="top:860px"><svg width="16" height="14" viewBox="0 0 16 14"><path d="M1 7l7-6 7 6M3 6v7h4V9h2v4h4V6" fill="none" stroke="#ccc" stroke-width="1.6"/></svg>Somewhere street 12</li>
  <li style="top:884px">City Name</li>
  <li style="top:908px">Country Name, 12345</li>
  <li style="top:932px"><svg width="14" height="14" viewBox="0 0 14 14"><circle cx="7" cy="7" r="6" fill="#ccc"/></svg>@velmoria</li>
  <li style="top:956px"><svg width="14" height="14" viewBox="0 0 14 14"><rect x="1" y="1" width="12" height="12" fill="#ccc"/></svg>social.velmoria.com/page</li>
</ul>

<div class="abs about-text"><div class="float"></div>Lorem ipsum dolor sit amet, consectetuer adipiscing elit, sed diam nonummy nibh euismod Lorem ipsum dolor sit amet, consectetuer adipiscing elit, sed diam nonummy nibh euismod tincidunt ut laoreet dolore magna aliquam erat volutpat. Ut wisi enim ad minim veniam, quis nostrud exerci tation ullamcorper suscipit lobortis nisl ut aliquip ex ea</div>
<div class="abs about-mark"><span></span></div>

<div class="field" style="top:806px;height:25px">your name</div>
<div class="field" style="top:839px;height:25px">your email</div>
<div class="field" style="top:876px;height:97px">your message</div>
<div class="abs required">* All Fields Are Required</div>
<div class="abs send">SEND</div>

<div class="abs bottombar"></div>
<div class="abs copyright">Copyright @ 2012 Velmoria</div>
<div class="abs bottom-links">About Us<span>|</span>Programs<span>|</span>Services<span>|</span>Contact</div>

</body>
</html>
```